Business card por a urban DJ, up scale audience target

Need a sober design, modern, conservative colors but i can consider some options, y play rnb, hip hop, EDM and top40.

Business card for contact and personal info, double sided, use logo attrached please; im 42 so i need a card acording to my age an target audience.

Target Market(s)

Adult people, up scale audience

Industry/Entity Type

Music Download

Contact Information for Business Card

Cel (318) 4207265518 www.lumadrift.com

Requirements
Must have
• open mind
Nice to have
• open mind
Should not have
• DJ

```html
<!DOCTYPE html>
<html lang="en">
<head>
<meta charset="utf-8">
<title>Lumadrift Business Card</title>
<link rel="stylesheet" href="https://fonts.googleapis.com/css2?family=Open+Sans:wght@400;700;800&display=swap">
<style>
  :root {
    --bg: #d9d9d9;
    --ink: #0a0a0a;
    --paper: #ffffff;
    --muted: #3a3a3a;
  }
  * { box-sizing: border-box; margin: 0; padding: 0; }
  html, body { width: 1200px; height: 900px; overflow: hidden; }
  body {
    background: var(--bg);
    font-family: "Open Sans", Arial, sans-serif;
    position: relative;
  }
  .card {
    position: absolute;
    width: 620px;
    height: 354px;
    overflow: hidden;
  }
  .card--front { left: 80px; top: 60px; background: var(--ink); color: var(--paper); }
  .card--back { left: 500px; top: 486px; background: var(--paper); color: var(--ink); }

  .wordmark {
    position: absolute;
    display: flex;
    align-items: center;
    gap: 14px;
    font-weight: 800;
    font-size: 88px;
    letter-spacing: 4px;
    line-height: 1;
  }
  .wordmark__square { width: 22px; height: 22px; background: currentColor; }
  .card--front .wordmark { left: 50px; top: 108px; }
  .card--back .wordmark { left: 52px; top: 150px; }

  .front-url {
    position: absolute;
    left: 54px; top: 212px;
    font-size: 21px;
    letter-spacing: 5px;
  }

  .equalizer { position: absolute; right: 0; }
  .card--front .equalizer { bottom: 0; width: 300px; height: 120px; }
  .card--back .equalizer { bottom: 60px; width: 320px; height: 150px; }

  .name-block {
    position: absolute;
    right: 28px; top: 20px;
    text-align: right;
  }
  .name-block__name { font-weight: 700; font-size: 20px; }
  .name-block__role { font-size: 10px; letter-spacing: 1px; color: var(--muted); }
  .name-tab {
    position: absolute;
    right: 0; top: 0;
    width: 16px; height: 44px;
    background: var(--ink);
  }

  .contact {
    position: absolute;
    left: 24px; top: 262px;
    font-size: 13px;
    line-height: 1.4;
  }
  .contact__row { display: flex; align-items: center; gap: 8px; }
  .contact__row svg { width: 10px; height: 10px; }
  .contact-rule {
    position: absolute;
    left: 24px; top: 312px;
    width: 250px; height: 2px;
    background: var(--ink);
  }
</style>
</head>
<body>

<section class="card card--front" aria-label="Card front">
  <div class="wordmark"><span class="wordmark__square"></span><span>LUMA</span></div>
  <p class="front-url">www.lumadrift.com</p>
  <svg class="equalizer" viewBox="0 0 300 120" preserveAspectRatio="none" fill="#ffffff" aria-hidden="true">
    <rect x="14" y="106" width="7" height="14"/><rect x="25" y="98" width="7" height="22"/>
    <rect x="36" y="102" width="7" height="18"/><rect x="47" y="110" width="7" height="10"/>
    <rect x="58" y="94" width="7" height="26"/><rect x="69" y="90" width="7" height="30"/>
    <rect x="80" y="100" width="7" height="20"/><rect x="91" y="86" width="7" height="34"/>
    <rect x="102" y="104" width="7" height="16"/><rect x="113" y="82" width="7" height="38"/>
    <rect x="124" y="92" width="7" height="28"/><rect x="135" y="78" width="7" height="42"/>
    <rect x="146" y="84" width="7" height="36"/><rect x="157" y="96" width="7" height="24"/>
    <rect x="168" y="74" width="7" height="46"/><rect x="179" y="80" width="7" height="40"/>
    <rect x="190" y="68" width="7" height="52"/><rect x="201" y="90" width="7" height="30"/>
    <rect x="212" y="64" width="7" height="56"/><rect x="223" y="72" width="7" height="48"/>
    <rect x="234" y="60" width="7" height="60"/><rect x="245" y="76" width="7" height="44"/>
    <rect x="256" y="54" width="7" height="66"/><rect x="267" y="62" width="7" height="58"/>
    <rect x="278" y="46" width="7" height="74"/><rect x="289" y="38" width="7" height="82"/>
  </svg>
</section>

<section class="card card--back" aria-label="Card back">
  <div class="name-tab"></div>
  <div class="name-block">
    <p class="name-block__name">Marco Vale</p>
    <p class="name-block__role">CEO</p>
  </div>
  <div class="wordmark"><span class="wordmark__square"></span><span>LUMA</span></div>
  <div class="contact">
    <p class="contact__row">
      <svg viewBox="0 0 10 10" aria-hidden="true"><rect x="2" y="0.5" width="6" height="9" rx="1" fill="none" stroke="#0a0a0a" stroke-width="1.2"/></svg>
      (318) 4207265518
    </p>
    <p class="contact__row">
      <svg viewBox="0 0 10 10" aria-hidden="true"><circle cx="5" cy="5" r="4.3" fill="none" stroke="#0a0a0a" stroke-width="1.2"/><path d="M0.7 5h8.6M5 0.7c-2.4 2.4-2.4 6.2 0 8.6M5 0.7c2.4 2.4 2.4 6.2 0 8.6" fill="none" stroke="#0a0a0a" stroke-width="0.8"/></svg>
      www.lumadrift.com
    </p>
  </div>
  <div class="contact-rule"></div>
  <svg class="equalizer" viewBox="0 0 320 150" preserveAspectRatio="none" fill="#0a0a0a" aria-hidden="true">
    <rect x="4" y="128" width="8" height="22"/><rect x="16" y="120" width="8" height="30"/>
    <rect x="28" y="132" width="8" height="18"/><rect x="40" y="116" width="8" height="34"/>
    <rect x="52" y="124" width="8" height="26"/><rect x="64" y="108" width="8" height="42"/>
    <rect x="76" y="118" width="8" height="32"/><rect x="88" y="102" width="8" height="48"/>
    <rect x="100" y="112" width="8" height="38"/><rect x="112" y="96" width="8" height="54"/>
    <rect x="124" y="106" width="8" height="44"/><rect x="136" y="88" width="8" height="62"/>
    <rect x="148" y="100" width="8" height="50"/><rect x="160" y="82" width="8" height="68"/>
    <rect x="172" y="92" width="8" height="58"/><rect x="184" y="74" width="8" height="76"/>
    <rect x="196" y="86" width="8" height="64"/><rect x="208" y="66" width="8" height="84"/>
    <rect x="220" y="78" width="8" height="72"/><rect x="232" y="58" width="8" height="92"/>
    <rect x="244" y="70" width="8" height="80"/><rect x="256" y="48" width="8" height="102"/>
    <rect x="268" y="60" width="8" height="90"/><rect x="280" y="38" width="8" height="112"/>
    <rect x="292" y="26" width="8" height="124"/><rect x="304" y="10" width="16" height="140"/>
  </svg>
</section>

</body>
</html>
```